Business Card for Vorla Parts Wholesale supplier

Hi There! I need a new business card for our company. We are specialized in selling Vorla parts, mostly we sell new LCD screens for Zelnar and Drelks. I would like to see that back in the design.

You can find the colors and logo's on our website: www.hartuvo.nl

Industry/Entity Type

Business

Contact Information for Business Card

My Details:
Tobias Lindqvist

Phone: 0031687203316
E-mail: Tobias@hartuvo.nl

Slogan: "Built For Every Repair"

Font styles to use
Sans Serif

Colors

Designer to choose colors to be used in the design.

Requirements
Must have
• A Black backside with the Hartuvo logo on it. The front side should be clean with only my contact details.
• But I'm also open for something really different or awesome!
Nice to have
• Remember that we are in the parts & repairing industry, So i'll be handing those business cards mainly to repair companies. Maybe you can do something with that thought :)

```html
<!DOCTYPE html>
<html lang="en">
<head>
<meta charset="utf-8">
<title>Hartuvo Business Card</title>
<link rel="stylesheet" href="https://fonts.googleapis.com/css2?family=Open+Sans:wght@400;600;700&display=swap">
<style>
  :root {
    --brand-orange: #f37021;
    --ink-dark: #1c1c1c;
    --ink-grey: #555555;
    --card-white: #ffffff;
    --divider: #cfcfcf;
    --backdrop: #e6e4e1;
  }
  * { box-sizing: border-box; margin: 0; padding: 0; }
  html, body {
    width: 1200px;
    height: 987px;
    overflow: hidden;
    background: var(--backdrop);
    font-family: "Open Sans", Arial, sans-serif;
  }
  .canvas { position: relative; width: 1200px; height: 987px; }

  .card-front {
    position: absolute;
    left: 292px; top: 130px;
    width: 616px; height: 322px;
    background: var(--card-white);
    border-bottom: 3px solid var(--ink-dark);
    box-shadow: 0 2px 6px rgba(0,0,0,0.18);
  }
  .front-accent-band {
    position: absolute;
    left: 292px; top: 457px;
    width: 616px; height: 23px;
    background: var(--brand-orange);
  }
  .wordmark {
    position: absolute;
    left: 63px; top: 148px;
    display: flex; align-items: center; gap: 12px;
  }
  .wordmark-dot {
    width: 40px; height: 40px;
    border-radius: 50%;
    background: var(--brand-orange);
  }
  .wordmark-name {
    font-size: 46px;
    font-weight: 600;
    color: var(--ink-dark);
    line-height: 1;
    letter-spacing: 0.5px;
  }
  .front-divider {
    position: absolute;
    left: 347px; top: 114px;
    width: 1px; height: 123px;
    background: var(--divider);
  }
  .contact-block {
    position: absolute;
    left: 376px; top: 116px;
  }
  .contact-name {
    font-size: 22px;
    font-weight: 600;
    color: var(--brand-orange);
    margin-bottom: 12px;
  }
  .contact-list { list-style: none; }
  .contact-list li {
    display: flex; align-items: center; gap: 8px;
    font-size: 15px;
    color: var(--ink-grey);
    height: 23.5px;
  }
  .contact-icon { width: 15px; height: 15px; flex: none; fill: var(--brand-orange); }

  .card-back {
    position: absolute;
    left: 292px; top: 505px;
    width: 615px; height: 352px;
    background: var(--brand-orange);
    box-shadow: 0 2px 6px rgba(0,0,0,0.18);
    color: var(--card-white);
    text-align: center;
  }
  .back-wordmark {
    position: absolute;
    left: 0; right: 0; top: 138px;
    font-size: 52px;
    font-weight: 600;
    line-height: 1;
  }
  .slogan {
    position: absolute;
    left: 0; right: 0; top: 281px;
    font-size: 19px;
    font-weight: 600;
  }
</style>
</head>
<body>
<main class="canvas">
  <section class="card-front">
    <div class="wordmark">
      <span class="wordmark-dot"></span>
      <span class="wordmark-name">hartuvo</span>
    </div>
    <div class="front-divider"></div>
    <div class="contact-block">
      <p class="contact-name">Tobias Lindqvist</p>
      <ul class="contact-list">
        <li>
          <svg class="contact-icon" viewBox="0 0 24 24" aria-hidden="true"><path d="M6.6 10.8a15.1 15.1 0 0 0 6.6 6.6l2.2-2.2c.3-.3.7-.4 1-.2 1.1.4 2.3.6 3.6.6.6 0 1 .4 1 1V20c0 .6-.4 1-1 1A17 17 0 0 1 3 4c0-.6.4-1 1-1h3.5c.6 0 1 .4 1 1 0 1.3.2 2.5.6 3.6.1.3 0 .7-.2 1z"/></svg>
          <span>0031687203316</span>
        </li>
        <li>
          <svg class="contact-icon" viewBox="0 0 24 24" aria-hidden="true"><path d="M2 5h20v14H2z" fill="var(--brand-orange)"/><path d="M3 6l9 7 9-7" fill="none" stroke="#fff" stroke-width="1.6"/></svg>
          <span>Tobias@hartuvo.nl</span>
        </li>
        <li>
          <svg class="contact-icon" viewBox="0 0 24 24" aria-hidden="true"><circle cx="12" cy="12" r="10"/><path d="M2 12h20M12 2c3 3 3 17 0 20M12 2c-3 3-3 17 0 20" fill="none" stroke="#fff" stroke-width="1.4"/></svg>
          <span>www.hartuvo.nl</span>
        </li>
      </ul>
    </div>
  </section>
  <div class="front-accent-band"></div>

  <section class="card-back">
    <p class="back-wordmark">hartuvo</p>
    <p class="slogan">Built For Every Repair</p>
  </section>
</main>
</body>
</html>
```